Coral Reach Yachting Flyer

Coral Reach Yachting (.com) is a high end luxury and private charter company in the Cayman Islands. All info can be found on our webiste. I currently have a 4 panel roll fold flyer (Can supply working file). I am looking for a new fresh look but also need some changes as we have changes some boats, added some new charter ideas etc.

Between our website and current flyer I think the designer will get the idea. I Welcome new and fresh, I do not need it to match current website, as I may get that changed to.

We are looking for high end and simple/clean and comunicate reliability and professional with a hint of fun in the sun of course. Not whacky and tacky!!

The current PDF's of the current flyer needs a fair bit of changing (For example scuba diving panel will come out and go into a new 1 panel flyer.) I will need 3-4 other flyers too, and a bunch of other stuff in future for new businesses, but starting with this one so I can pick a designer (This is my 1st go with pixel bazaar, always did my own work, but am too busy and am not very good with creativity)

I have logo, support pictures, etc. Have uploaded the basics can email more info and changes after I find a designer. Lots of our boat pictures can be found at http://coralreachyachting.example/downloads/maple.zip

Also, we want a panel dedicated to wavedart.example as our big boat now has one onboard and our smaller boat (23') will have two and that will be a dedicated panel (Replace scuba) offering a "Wavedart Ultra Reef trip" (I will supply more info on that, once I pick a designer).

Target Market(s)

High end groups. The groups or families that will spend more to get more!!

Industry/Entity Type

It Company

```html
<!DOCTYPE html>
<html lang="en">
<head>
<meta charset="utf-8">
<title>Coral Reach Yachting Flyer</title>
<link href="https://fonts.googleapis.com/css2?family=Arimo:wght@400;700&display=swap" rel="stylesheet">
<style>
:root{
  --bg:#e9e6e1;
  --paper:#ffffff;
  --orange:#f0623a;
  --gold:#f7b71f;
  --teal:#145b51;
  --blue-head:#4a7fbd;
  --text:#4a4a4a;
  --call:#f5a81c;
  --sky-top:#5b93d6;
  --sky-light:#b9d6ef;
  --cloud:#eef4fa;
  --lagoon:#35c3c8;
  --lagoon-light:#7fe0e2;
  --sea-deep:#0e6f8c;
  --navy:#0d4f78;
  --hull:#f4f6f7;
}
*{box-sizing:border-box;margin:0;padding:0}
html,body{width:1200px;height:802px;overflow:hidden;background:var(--bg);font-family:"Arimo",Arial,sans-serif}
.canvas{position:relative;width:1200px;height:802px}
.flyer{position:absolute;left:98px;top:93px;width:1002px;height:609px;background:var(--paper);box-shadow:0 4px 14px rgba(0,0,0,.25)}
.band-top{position:absolute;left:0;top:0;width:100%;height:18px;background:var(--orange)}
.band-bottom{position:absolute;left:0;bottom:0;width:100%;height:17px;background:var(--gold)}
.panel{position:absolute;top:18px;height:574px;width:250px}
.p1{left:0}.p2{left:250px;background:var(--teal)}.p3{left:500px}.p4{left:750px;width:252px}
.photo{position:absolute}

/* photo areas, each in the tones of the scene it stands for */
.photo-speedboat{background:linear-gradient(180deg,var(--sky-top) 0%,var(--sky-light) 22%,var(--cloud) 36%,#cfe6ee 42%,var(--lagoon-light) 50%,var(--lagoon) 72%,#1f9aa6 100%)}
.photo-stingray{background:radial-gradient(ellipse at 40% 55%,#e9c9b6 0%,#9fc9d6 30%,transparent 55%),linear-gradient(135deg,#8fe6ee 0%,var(--lagoon) 55%,#1d9fb6 100%)}
.photo-dock{background:linear-gradient(180deg,#6d8fa6 0%,#9bb3c4 30%,var(--hull) 55%,#cfd9e0 75%,#3a5566 100%)}
.photo-wake{background:linear-gradient(180deg,#9fc6e6 0%,#d7e7f3 30%,#6aa8cf 45%,#f2f6f9 62%,#3e8fbf 100%)}
.photo-scooter{background:radial-gradient(ellipse at 72% 62%,#f4d23a 0%,#e8c52f 18%,transparent 34%),radial-gradient(ellipse at 28% 45%,#e7bfa6 0%,#d9a88d 22%,transparent 42%),linear-gradient(160deg,#3cc7d7 0%,#29b5cc 50%,#1896b5 100%)}
.photo-dive{background:linear-gradient(205deg,#3a7fd0 0%,#9cc7ee 22%,transparent 38%),linear-gradient(115deg,#49cdd7 0%,#23a9c3 55%,transparent 72%),linear-gradient(115deg,#fff 60%,#e7eef2 100%)}
.photo-bow-guest{background:linear-gradient(180deg,#5f9ad8 0%,#c8def0 35%,#eef3f7 55%,#f7f1ea 75%,#d9e2e8 100%)}
.photo-cover{background:linear-gradient(180deg,var(--sky-top) 0%,#8db8e2 18%,var(--cloud) 30%,#a9cbe8 36%,#7fb4dd 40%,var(--hull) 44%,#e4ecef 54%,#c6d6dc 60%,#2f9a9e 64%,#1f7f9a 75%,var(--navy) 88%,#0b3f63 100%)}

h2.things{position:absolute;left:19px;top:284px;width:215px;font-size:14.5px;font-weight:400;line-height:19px;color:var(--blue-head)}
ul.activities{position:absolute;left:20px;top:330px;list-style:none;font-size:11.2px;line-height:14.4px;color:var(--text)}
ul.activities li::before{content:"•";color:var(--blue-head);margin-right:5px}
.trip-title{position:absolute;left:20px;top:50px;font-size:26px;line-height:30px;color:#fff;font-weight:400}
.divider{position:absolute;left:0;top:317px;width:250px;height:6px;background:#e9f2f1}
.trip-copy{position:absolute;left:19px;top:347px;width:200px;font-size:8.6px;line-height:9.6px;color:#fff;text-align:justify}
.trip-copy p{margin-bottom:9px}
h2.why{position:absolute;left:22px;top:26px;font-size:14px;font-weight:400;color:var(--blue-head)}
.why-copy{position:absolute;left:22px;top:55px;width:206px;font-size:9.1px;line-height:13.3px;color:var(--text);text-align:justify}
.call{position:absolute;left:20px;top:466px}
.call h3{font-size:16px;font-weight:700;color:var(--call);margin-bottom:4px}
.call p{font-size:12.8px;line-height:18px;color:var(--text)}
.tagline{position:absolute;left:18px;top:17px;font-size:17.5px;color:#fff;font-weight:400}
.brand{position:absolute;left:32px;top:435px;width:185px;height:121px;background:#fff;display:flex;align-items:center;justify-content:center;gap:8px}
.brand .mark{width:14px;height:14px;border-radius:50%;background:var(--orange)}
.brand .name{font-size:14px;font-weight:700;color:var(--teal);line-height:17px}
</style>
</head>
<body>
<div class="canvas">
  <div class="flyer">
    <div class="band-top"></div>

    <section class="panel p1">
      <div class="photo photo-speedboat" style="left:0;top:0;width:250px;height:161px" role="img" aria-label="Speedboat cruising over turquoise water under a cloudy sky"></div>
      <div class="photo photo-stingray" style="left:83px;top:161px;width:167px;height:114px" role="img" aria-label="Woman swimming with a stingray"></div>
      <h2 class="things">Things to do with us, in Grand Cayman</h2>
      <ul class="activities">
        <li>Swimming and Snorkeling</li>
        <li>Bioluminescence Night Diving</li>
        <li>Sunken Tern Snorkelling</li>
        <li>Deep Sea Fishing</li>
        <li>Starfish Point</li>
        <li>Harbor Bbq Tuesdays</li>
        <li>Purchase a vacation home</li>
        <li>Family Beach Portraits</li>
        <li>Rent your own vacation villa</li>
      </ul>
      <div class="photo photo-dock" style="left:0;top:472px;width:110px;height:80px" role="img" aria-label="Motor boat moored at a dock"></div>
      <div class="photo photo-wake" style="left:114px;top:477px;width:134px;height:88px" role="img" aria-label="Boat speeding away across the water"></div>
    </section>

    <section class="panel p2">
      <h1 class="trip-title">Wavedart<br>Ultra<br>Reef trip</h1>
      <div class="photo photo-scooter" style="left:0;top:161px;width:250px;height:156px" role="img" aria-label="Father and child riding a yellow underwater scooter"></div>
      <div class="divider"></div>
      <div class="trip-copy">
        <p>Lots of New Toys<br>aboard Island Drifter</p>
        <p>From the exciting Wavedart, leaping off the top deck, swinging on the rope swing, cruising with the Jetski, relaxing in the Hammock or fishing in the gorgeous North Sound.</p>
        <p>You are guaranteed to have an incredible time with friends and family aboard Island Drifter.</p>
        <p>Compliment your trip with our gourment catering menu, on board cash bar, including local and international beer, wines, spirits and local rum punch.</p>
        <p>PRE-BOOK any of our extras while onboard Island Drifter.</p>
      </div>
    </section>

    <section class="panel p3">
      <h2 class="why">Why Choose us?</h2>
      <p class="why-copy">We are a Caymanian owned company striving to offer something different to locals and tourists alike. For the past 30 years the founder of this company has enjoyed the unparalleled beauty of the Cayman Islands &amp; surrounding waters. Water skiing, diving, Rum Point...</p>
      <div class="photo photo-dive" style="left:0;top:164px;width:250px;height:167px" role="img" aria-label="Diver leaping off a yacht deck into clear water"></div>
      <div class="photo photo-bow-guest" style="left:119px;top:332px;width:131px;height:103px" role="img" aria-label="Guest relaxing on the bow of a yacht"></div>
      <div class="call">
        <h3>Call us now!</h3>
        <p>345-555-0148</p>
        <p>info@CoralReachYachting.example</p>
        <p>www.coralreachyachting.example</p>
      </div>
    </section>

    <section class="panel p4">
      <div class="photo photo-cover" style="left:0;top:0;width:252px;height:574px" role="img" aria-label="White yacht bow above deep blue sea under a cloudy sky"></div>
      <h2 class="tagline">Show Your Love With Us</h2>
      <div class="brand">
        <span class="mark"></span>
        <span class="name">Coral Reach<br>Yachting</span>
      </div>
    </section>

    <div class="band-bottom"></div>
  </div>
</div>
</body>
</html>
```